Design my site www.brieflyledger.com

So here is what I am thinking in terms of design:

https://plenvo.com

https://www.skyluxair.com

http://kalvex.com/harbor-plaza-tower/

I want the theme to be white and blue (royal blue). I attached a paint picture of what I would like the site to look like in terms of placing the text. Generally, what I like about the sites above is that they are simple, you can navigate easily and have some kind of idea of what's going on by looking at the center (picture and motto). Let's establish a clear understanding of how the functional part of the site would look like. Please see the picture attached.

I want to keep it simple: On top would be the Name 'BRIEFLY ledger", somewhere to the right on top on the page would be 'Sign in" button.

In the center would be a picture (maybe a video) with the Motto (on top of it all in capital) OBSERVE NAVIGATE DECIDE and below would be the "sign up now"

Below the picture (like on kalvex.com site) or to the left on top of the page would be "About Us', "Press" "Contact Us' buttons.

Then once the user gets to his page his got 3 tabs " Press Headlines", "Events", " Briefings".

we would keep the same format I only have on the site, but separate for every Tab.

I do not want the user to get distracted. I also want him to be able to access the page though mobile phone and be able to get automatic updates just like Zorvan Pings without having to sign in daily.

The landing page must be minimalist yet with business/corporate feel where users can navigate easily and a "what you see is what you get" approach. You want an image or video (personally I prefer the video.. it does capture the users attention instantly, as long as it is an interesting video), with your taglines in it.

Sections available to public: About Us, Contact Us, Landing Page with Signup Option

Private: Public Sections + User Account Page, Tabs for (Events, Press Headlines, Briefings)

Target Market(s)

PR/media monitoring/diplomatic community

Coding

Coded - Design and coding required

Number of Pages Required

1 page

Font styles to use
Serif
Sans Serif

Colors
0255a3
ec1f27

Requirements
Must have
• a simple landing page, that is user friendly.
Nice to have
• a video with the explanation of how to navigate the site
Should not have
• too many colors, graphs etc.

```html
<!DOCTYPE html>
<html lang="en">
<head>
<meta charset="utf-8">
<title>Briefly Ledger</title>
<link rel="stylesheet" href="https://fonts.googleapis.com/css2?family=Arimo:wght@400;700&display=swap">
<style>
  :root {
    --royal: #0255a3;
    --royal-deep: #0650a8;
    --sky: #2a85dc;
    --white: #ffffff;
    --panel: #f4f4f4;
    --social: #4a6ea8;
    --button-text: #3a66ad;
    --divider: #1d5ea8;
  }
  * { box-sizing: border-box; margin: 0; padding: 0; }
  html, body { width: 1200px; height: 715px; overflow: hidden; }
  body { font-family: "Arimo", Arial, sans-serif; background: var(--white); position: relative; }

  .site-header { position: absolute; top: 0; left: 0; width: 1200px; height: 61px; background: var(--white); }
  .brand { position: absolute; left: 20px; top: 0; height: 61px; display: flex; align-items: center; gap: 12px; }
  .brand-mark { width: 30px; height: 30px; background: var(--royal); border-radius: 4px; }
  .brand-name { font-size: 22px; font-weight: 700; color: var(--royal); letter-spacing: 0.3px; }

  .social-bar { position: absolute; left: 883px; top: 0; width: 189px; height: 61px; background: var(--panel);
    border-left: 1px solid #e2e2e2; display: flex; align-items: center; justify-content: center; gap: 2px; }
  .social-link { width: 30px; height: 31px; background: var(--social); display: block; }

  .sign-in { position: absolute; left: 1072px; top: 0; width: 128px; height: 61px; background: var(--royal);
    color: var(--white); font-size: 14px; font-weight: 700; display: flex; align-items: center; justify-content: center;
    text-decoration: none; letter-spacing: 0.3px; }

  .hero { position: absolute; top: 61px; left: 0; width: 1200px; height: 595px; overflow: hidden; }
  .hero-photo { position: absolute; inset: 0;
    background: linear-gradient(160deg, #5b6479 0%, #3d4558 35%, #6a6c74 60%, #4a5266 100%); }
  .hero-shade { position: absolute; inset: 0; background: rgba(20, 28, 60, 0.35); }

  .hero-title { position: absolute; left: 0; right: 0; top: 246px; display: flex; align-items: center; justify-content: center; gap: 14px; }
  .hero-title .rule { width: 101px; height: 2px; background: var(--white); }
  .hero-title h1 { color: var(--white); font-size: 63px; font-weight: 700; letter-spacing: 1px; line-height: 1; }
  .tagline { position: absolute; left: 0; right: 0; top: 331px; text-align: center; color: var(--white);
    font-size: 28px; font-weight: 400; letter-spacing: 0.3px; }
  .cta { position: absolute; left: 486px; top: 389px; width: 229px; height: 49px; background: var(--white);
    color: var(--button-text); font-size: 19px; font-weight: 700; display: flex; align-items: center; justify-content: center;
    text-decoration: none; letter-spacing: 0.5px; }

  .main-nav { position: absolute; top: 656px; left: 0; width: 1200px; height: 59px; display: flex; }
  .nav-item { flex: 1; display: flex; align-items: center; justify-content: center; gap: 16px; background: var(--sky);
    color: var(--white); font-size: 19px; font-weight: 700; text-decoration: none; letter-spacing: 0.3px; }
  .nav-item + .nav-item { border-left: 1px solid var(--divider); }
  .nav-item.is-active { background: var(--royal-deep); }
  .nav-item svg { display: block; }
</style>
</head>
<body>
  <header class="site-header">
    <a class="brand" href="#">
      <span class="brand-mark" aria-hidden="true"></span>
      <span class="brand-name">BRIEFLY LEDGER</span>
    </a>
    <nav class="social-bar" aria-label="Social networks">
      <a class="social-link" href="#" aria-label="Social network 1"></a>
      <a class="social-link" href="#" aria-label="Social network 2"></a>
      <a class="social-link" href="#" aria-label="Social network 3"></a>
      <a class="social-link" href="#" aria-label="Social network 4"></a>
      <a class="social-link" href="#" aria-label="Social network 5"></a>
    </nav>
    <a class="sign-in" href="#">SING IN</a>
  </header>

  <section class="hero">
    <div class="hero-photo" role="img" aria-label="Aerial photograph of a dense city business district with high-rise towers"></div>
    <div class="hero-shade"></div>
    <div class="hero-title">
      <span class="rule"></span>
      <h1>BRIEFLY LEDGER</h1>
      <span class="rule"></span>
    </div>
    <p class="tagline">OBSERVE • NAVIGATE • DECIDE</p>
    <a class="cta" href="#">SING UP NOW</a>
  </section>

  <nav class="main-nav" aria-label="Main">
    <a class="nav-item" href="#">
      <svg width="34" height="34" viewBox="0 0 34 34" fill="none" stroke="#fff" stroke-width="2">
        <circle cx="17" cy="17" r="15.5"/>
        <circle cx="17" cy="13" r="5"/>
        <path d="M7.5 27c2-5 5.5-7.5 9.5-7.5s7.5 2.5 9.5 7.5"/>
      </svg>
      ABOUT US
    </a>
    <a class="nav-item is-active" href="#">
      <svg width="36" height="26" viewBox="0 0 36 26" fill="none" stroke="#fff" stroke-width="2">
        <rect x="5" y="1" width="30" height="24" rx="2"/>
        <path d="M5 6H1v16a3 3 0 0 0 6 0"/>
        <rect x="10" y="5" width="9" height="7" fill="#fff"/>
        <path d="M22 6h9M22 10h9M10 15h21M10 19h21"/>
      </svg>
      PRESS
    </a>
    <a class="nav-item" href="#">
      <svg width="28" height="30" viewBox="0 0 28 30" fill="none" stroke="#fff" stroke-width="2">
        <rect x="4" y="1" width="23" height="28"/>
        <path d="M1 7h5M1 15h5M1 23h5"/>
        <circle cx="16" cy="11" r="4" fill="#fff"/>
        <path d="M9 23c1-4.5 4-6.5 7-6.5s6 2 7 6.5z" fill="#fff"/>
      </svg>
      CONTACT US
    </a>
  </nav>
</body>
</html>
```